Advertising company unique advertising platform

we need a logo design for a new company based in Australia Melbourne. We develop innovated advertising platform where consumer can use this platform to get regular discount, as business owner they can use this platform for free advertisement. Payment for this advertisement platform only payable every two weeks, when I generate revenue for their business

Industry/Entity Type

Advertising

Contact Information for Business Card

Dale Morven | Co-Founder |Managing Director
Suite 718 240 Wattlebrook Lane Melbourne Vic 3000

ABN 38 614 207 923
Tel: +61 0487 259 318 | Email: dale.morven@plivorantu.com

Font styles to use
Decorative
Script

Requirements
Must have
• Try few different design and some round corner business card
Should not have
• One round corner business card...try 4 different colour background not only black, make sure two side is designed. Be creative so imagine you are giving this to a client make sure has wow factor, if you can also try one design with engrave like all the logo, words look 3d feel
• The word Advertising Platform use attached file font

```html
<!DOCTYPE html>
<html lang="en">
<head>
<meta charset="utf-8">
<title>Kestrel Market – Business Card</title>
<link href="https://fonts.googleapis.com/css2?family=Roboto:wght@400;500;700&display=swap" rel="stylesheet">
<style>
  :root {
    --page-bg: #ecebe8;
    --card-dark: #262626;
    --ink: #1f1f1f;
    --light-text: #e6e6e6;
    --brand-orange: #f07a2a;
    --grad-red: #e9473a;
    --grad-orange: #f0782c;
    --grad-yellow: #f2c54a;
    --grad-blue: #29b9ec;
    --grad-lilac: #8aa6dc;
  }
  * { margin: 0; padding: 0; box-sizing: border-box; }
  html, body {
    width: 1200px; height: 886px; overflow: hidden;
    background: var(--page-bg);
    font-family: "Roboto", Arial, sans-serif;
  }
  .canvas {
    width: 1200px; height: 886px;
    display: flex; align-items: center; justify-content: center; gap: 40px;
  }
  .card {
    position: relative;
    width: 560px; height: 320px;
    border-radius: 24px;
    overflow: hidden;
    box-shadow: 0 10px 28px rgba(0,0,0,.22);
  }
  /* Back side */
  .card-back {
    background: var(--card-dark);
    display: flex; flex-direction: column; align-items: center; justify-content: center;
  }
  .brand {
    display: flex; align-items: center; gap: 16px;
    margin-top: 10px;
  }
  .brand-dot {
    width: 54px; height: 54px; border-radius: 50%;
    background: var(--brand-orange);
  }
  .brand-name {
    font-weight: 700; font-size: 38px; color: var(--brand-orange);
    letter-spacing: .5px;
  }
  .website {
    margin-top: 58px;
    color: var(--light-text); font-size: 13px; letter-spacing: 6px;
  }
  /* Front side */
  .card-front {
    background:
      radial-gradient(circle at 52% 40%, var(--grad-yellow) 0%, var(--grad-orange) 38%, var(--grad-red) 78%);
    color: var(--ink);
  }
  .front-blue {
    position: absolute; top: 0; right: 0; width: 150px; height: 100%;
    background: linear-gradient(180deg, var(--grad-lilac), var(--grad-blue));
    clip-path: polygon(40% 0, 100% 0, 100% 100%, 0 100%, 35% 55%);
  }
  .front-mark {
    position: absolute; right: 70px; bottom: 34px;
    width: 150px; height: 150px; border-radius: 50%;
    background: var(--ink);
  }
  .contact { position: absolute; left: 40px; top: 34px; }
  .person-name { font-size: 19px; font-weight: 700; letter-spacing: .3px; }
  .person-role { font-size: 14px; font-weight: 500; margin-top: 2px; }
  .details { margin-top: 34px; font-size: 14px; line-height: 19px; }
  .details .line { display: flex; align-items: center; gap: 8px; }
  .details svg { width: 12px; height: 12px; fill: var(--ink); }
</style>
</head>
<body>
  <main class="canvas">
    <section class="card card-back">
      <div class="brand">
        <span class="brand-dot"></span>
        <span class="brand-name">Kestrel Market</span>
      </div>
      <div class="website">www.plivorantu.com</div>
    </section>

    <section class="card card-front">
      <div class="front-blue"></div>
      <div class="front-mark"></div>
      <div class="contact">
        <div class="person-name">DALE MORVEN</div>
        <div class="person-role">Co-Founder | Managing Director</div>
        <div class="details">
          <div class="line">Plivo Rantu</div>
          <div class="line">ABN 38 614 207 923</div>
          <div class="line">Suite 718 240 Wattlebrook Lane</div>
          <div class="line">Melbourne Vic 3000</div>
          <div class="line">
            <svg viewBox="0 0 24 24" aria-hidden="true"><path d="M6.6 10.8a15.1 15.1 0 0 0 6.6 6.6l2.2-2.2a1 1 0 0 1 1-.25 11.4 11.4 0 0 0 3.6.57 1 1 0 0 1 1 1V20a1 1 0 0 1-1 1A17 17 0 0 1 3 4a1 1 0 0 1 1-1h3.5a1 1 0 0 1 1 1c0 1.25.2 2.45.57 3.57a1 1 0 0 1-.25 1z"/></svg>
            +61 0487 259 318
          </div>
          <div class="line">
            <svg viewBox="0 0 24 24" aria-hidden="true"><path d="M2 5h20v14H2z M2 5l10 8 10-8" stroke="#e9473a" stroke-width="1.5"/></svg>
            dale.morven@plivorantu.com
          </div>
        </div>
      </div>
    </section>
  </main>
</body>
</html>
```